Business card for Eyelash extension salon in Beverly Hills,California USA

We need new business card for our salon in Beverly Hills. The salon name is 'Lashvera' . We would like to have...Business name: Lashvera Name of person: will provide later Address 4720 N.Alder Crest Ave Beverly Hills , CA 90210 Phone: will provide later (Text only) Web: www.lashverastudio.example Snapgrid icon, Circlebook icon follow us for seasonal campaign and news @lashverastudiolounge Design should look elegant, high-end, clean, simple, cohesive with my brand. Please refer my brand board. Business name color will be metallic bronzy color. Im thinking grey background or white background. Thanks

Target Market(s)

25-35. Gender neutral. People who are in Entertainment business industry.
This is High-end Eyelash extension salon in Beverly Hills

Industry/Entity Type

Beauty Salon

Contact Information for Business Card

Business name: Lashvera
Name of person: will provide later
Address 4720 N.Alder Crest Ave Beverly Hills , CA 90210
Phone: will provide later (Text only)
Web: www.lashverastudio.example
Snapgrid icon, Circlebook icon
follow us for seasonal campaign and news @lashverastudiolounge

Requirements
Must have
• Beautiful, elegant, clean and simple look but very attractive and modern
Should not have
• We don't like too clutter, too busy designs.

```html
<!DOCTYPE html>
<html lang="en">
<head>
<meta charset="utf-8">
<title>Lashvera Beverly Hills – Business Card</title>
<link href="https://fonts.googleapis.com/css2?family=Cormorant+Garamond:wght@400;500&family=Playfair+Display:wght@700&family=Josefin+Sans:wght@400&display=swap" rel="stylesheet">
<style>
  :root{
    --backdrop:#e4e4e4;
    --paper:#ffffff;
    --foil-light:#eeeeee;
    --foil-mid:#c9c9c9;
    --foil-dark:#a9a9a9;
    --bronze:#85603f;
    --ink-grey:#6a6a6a;
    --label-grey:#9a9a9a;
    --rule:#b9a48f;
  }
  *{margin:0;padding:0;box-sizing:border-box}
  html,body{width:1200px;height:960px;overflow:hidden;background:var(--backdrop)}
  .canvas{position:relative;width:1200px;height:960px}

  .card{position:absolute;width:601px;height:342px;
    background:linear-gradient(135deg,var(--foil-light) 0%,var(--foil-mid) 45%,var(--foil-light) 70%,var(--foil-dark) 100%)}
  .card__face{position:absolute;left:14px;top:12px;width:571px;height:313px;background:var(--paper)}
  .card--info{left:302px;top:123px}
  .card--brand{left:300px;top:495px}

  .holder{position:absolute;right:361px;top:128px;text-align:right}
  .holder__name{font-family:"Playfair Display",serif;font-weight:700;color:var(--bronze);font-size:24px;letter-spacing:1px;line-height:26px}
  .holder__role{font-family:"Playfair Display",serif;font-weight:700;color:var(--label-grey);font-size:14px;letter-spacing:1.5px;line-height:16px}

  .divider{position:absolute;left:233px;top:106px;width:1px;height:98px;background:var(--rule)}

  .contact{position:absolute;left:256px;top:104px;font-family:"Cormorant Garamond",serif;font-weight:500;color:var(--ink-grey);font-size:15px;line-height:18px;list-style:none}
  .contact__gap{margin-top:5px}

  .social{position:absolute;left:0;right:0;top:256px;display:flex;justify-content:center;align-items:center;gap:5px;
    font-family:"Cormorant Garamond",serif;font-weight:500;color:var(--ink-grey);font-size:14px;white-space:nowrap}
  .social__net{display:flex;align-items:center;gap:3px;font-size:12px;color:var(--label-grey)}
  .social__dot{width:9px;height:9px;border-radius:50%;background:var(--label-grey)}
  .social__text{margin-left:4px}

  .brand{position:absolute;left:0;right:0;top:70px;text-align:center}
  .brand__name{font-family:"Cormorant Garamond",serif;font-weight:400;color:var(--bronze);font-size:112px;line-height:130px;letter-spacing:1px}
  .brand__place{font-family:"Josefin Sans",sans-serif;color:var(--bronze);font-size:12px;letter-spacing:2.4px;margin-top:0;padding-left:150px}
</style>
</head>
<body>
<main class="canvas">

  <section class="card card--info" aria-label="Card front with contact details">
    <div class="card__face">
      <div class="holder">
        <p class="holder__name">MIREYA</p>
        <p class="holder__role">OWNER</p>
      </div>
      <div class="divider"></div>
      <ul class="contact">
        <li>4720 N.Alder Crest Ave</li>
        <li>Beverly Hills, CA 90210</li>
        <li class="contact__gap">310.555.0148</li>
        <li>studio@lashverastudio.example</li>
        <li>www.lashverastudio.example</li>
      </ul>
      <p class="social">
        <span class="social__net"><span class="social__dot"></span>Circlebook</span>
        <span class="social__net"><span class="social__dot"></span>Snapgrid</span>
        <span class="social__net"><span class="social__dot"></span>Stopby</span>
        <span class="social__text">follow us for seasonal campaign &amp; news @lashverastudiolounge</span>
      </p>
    </div>
  </section>

  <section class="card card--brand" aria-label="Card back with salon name">
    <div class="card__face">
      <div class="brand">
        <p class="brand__name">Lashvera</p>
        <p class="brand__place">BEVERLY HILLS</p>
      </div>
    </div>
  </section>

</main>
</body>
</html>
```